BOLD & MINIMALIST DESIGN NEEDED

We want a very bold but minimalistic business card design that is impactful and utilizes both sides of the business card. Our current logo is included for your use.

We want bold fonts and good use of negative space. We don't want the logo to overpower the design.

Target Market(s)

Professionals who are building new commercial buildings.

Industry/Entity Type

Construction

Contact Information for Business Card

Name, Title, email, office phone, cell phone, website

Font styles to use
Serif
Sans Serif

Requirements
Must have
• Bold design!

```html
<!DOCTYPE html>
<html lang="en">
<head>
<meta charset="utf-8">
<title>Ridgeline Design + Build — Business Card</title>
<link rel="stylesheet" href="https://fonts.googleapis.com/css2?family=Montserrat:wght@400;500;800&display=swap">
<style>
  :root {
    --stage: #3b3b3d;
    --brand-green: #84c441;
    --ink: #0d0e10;
    --paper: #ffffff;
  }
  * { box-sizing: border-box; margin: 0; padding: 0; }
  html, body { width: 1200px; height: 689px; overflow: hidden; }
  body {
    background: var(--stage);
    font-family: "Montserrat", Arial, sans-serif;
    position: relative;
  }
  .card {
    position: absolute;
    top: 194px;
    width: 525px;
    height: 300px;
    border-radius: 18px;
    overflow: hidden;
  }
  .card--front { left: 50px; background: var(--brand-green); }
  .card--back { left: 625px; background: var(--paper); }

  .front-brand {
    position: absolute;
    inset: 0;
    display: flex;
    flex-direction: column;
    align-items: center;
    justify-content: center;
    color: var(--paper);
    font-weight: 800;
    text-transform: uppercase;
    line-height: 1;
  }
  .front-brand__name { font-size: 58px; letter-spacing: 1px; }
  .front-brand__tag { font-size: 22px; letter-spacing: 9px; margin-top: 10px; }

  .back-art { position: absolute; inset: 0; }

  .back-brand {
    position: absolute;
    right: 34px;
    top: 26px;
    text-align: right;
    color: var(--ink);
    font-weight: 800;
    text-transform: uppercase;
    line-height: 1;
  }
  .back-brand__name { font-size: 32px; }
  .back-brand__tag { font-size: 11px; letter-spacing: 6px; margin-top: 6px; }

  .contact {
    position: absolute;
    left: 30px;
    bottom: 18px;
    color: var(--paper);
  }
  .contact__name {
    color: var(--brand-green);
    font-weight: 800;
    font-size: 22px;
    line-height: 26px;
    letter-spacing: 0.5px;
    text-transform: uppercase;
  }
  .contact__title {
    font-size: 12px;
    font-weight: 500;
    letter-spacing: 0.5px;
    line-height: 16px;
    margin: 0 0 10px;
  }
  .contact__list { list-style: none; }
  .contact__item {
    display: flex;
    align-items: center;
    gap: 8px;
    font-size: 12px;
    line-height: 18px;
  }
  .contact__icon { width: 11px; height: 11px; fill: var(--brand-green); flex: none; }

  .address {
    position: absolute;
    right: 30px;
    bottom: 40px;
    color: var(--paper);
    font-size: 12px;
    line-height: 18px;
    text-align: right;
  }
</style>
</head>
<body>

<section class="card card--front" aria-label="Card front">
  <div class="front-brand">
    <span class="front-brand__name">Ridgeline</span>
    <span class="front-brand__tag">Design + Build</span>
  </div>
</section>

<section class="card card--back" aria-label="Card back">
  <svg class="back-art" viewBox="0 0 525 300" preserveAspectRatio="none" aria-hidden="true">
    <path d="M0,300 L0,146 C160,126 340,110 525,90 L525,300 Z" fill="var(--ink)"/>
    <path d="M12,138 C100,122 200,110 300,104 C200,114 100,128 12,143 Z" fill="var(--ink)"/>
    <path d="M415,100 C455,94 495,82 525,70 L525,77 C495,90 455,98 415,100 Z" fill="var(--brand-green)"/>
  </svg>

  <div class="back-brand">
    <div class="back-brand__name">Ridgeline</div>
    <div class="back-brand__tag">Design + Build</div>
  </div>

  <div class="contact">
    <div class="contact__name">Daniel Reyes</div>
    <div class="contact__title">OWNER-CEO</div>
    <ul class="contact__list">
      <li class="contact__item">
        <svg class="contact__icon" viewBox="0 0 12 12"><path d="M1,4 C1,2 3,1 6,1 C9,1 11,2 11,4 L9,5 L8,3.5 C7,3.2 5,3.2 4,3.5 L3,5 Z M2.5,6 L9.5,6 L10.5,11 L1.5,11 Z"/></svg>
        123 456 789
      </li>
      <li class="contact__item">
        <svg class="contact__icon" viewBox="0 0 12 12"><path d="M3,0.5 H9 V11.5 H3 Z M4,1.5 V9.5 H8 V1.5 Z"/></svg>
        123 456 789
      </li>
      <li class="contact__item">
        <svg class="contact__icon" viewBox="0 0 12 12"><path d="M0.5,2.5 H11.5 V9.5 H0.5 Z M1.5,3.2 L6,6.6 L10.5,3.2 Z"/></svg>
        info@yourgmail.com
      </li>
      <li class="contact__item">
        <svg class="contact__icon" viewBox="0 0 12 12"><circle cx="6" cy="6" r="5.5"/></svg>
        www.yourwebsite.com
      </li>
    </ul>
  </div>

  <div class="address">Your address, City<br>State, Zip 1234</div>
</section>

</body>
</html>
```